Kestrel Motion LLC Sports Therapy and Soft Tissue Injury solutions

We are a company that specializes in Sports Therapy, Physical therapy, muscular rehab, nutrition plans, and personal training. Kestrel Motion travels around the country and world treating athletes and people in the workforce that have Soft Tissue injuries. We are legally partnered with VMR(Vantor Muscle Recovery/vantorrecovery.example) in treating endurance athletes ex. SteelRidge triathalon. We educate our patients on how to sustain a healthy lifestyle.We need a web design that has a Home page summarizing our services, a Physical therapy page, a Personal training and nutrition page. Our ultimate goal is to build relationships with fitness centers, training facilities, and companies that are implementing preventative health measures for their employees. We want to incorporate the VMR logo and Steelridge logo attached in the website but, we want to use our own name (Kestrel Motion LLC) as the main draw. We will provide literature for the website.

Target Market(s)

Grindlane training gyms, Fitness centers, Dance studios, Companies looking for Corporate Wellness programs

Industry/Entity Type

Health And Wellness

Number of Pages Required

4 page

Font styles to use
Sans Serif

Requirements
Must have
• Stock Photos of Athletes training. Examples of Endurance Athletes and Cross training. A mesh of as many sports and training methods as possible. We are a new company and don't have many photos. Easy accessibility to change and add text as the company grows. Vantor Muscle recovery logo incorporated in the back ground of the website. Always visible but does not take over the web page
Nice to have
• Sleek and cool, and masculine design. We want the website to stand out without focusing on one individual. We want to use the website to brand the company (Kestrel Motion LLC) with easy access to social media platforms

```html
<!DOCTYPE html>
<html lang="en">
<head>
<meta charset="utf-8">
<title>Kestrel Motion LLC</title>
<link href="https://fonts.googleapis.com/css2?family=Oswald:wght@400;500;700&family=Open+Sans:wght@400;600;700&display=swap" rel="stylesheet">
<style>
:root{
  --ink:#111;
  --red:#d3201f;
  --dark:#1b1b1b;
  --nav:#222;
  --grey:#555;
  --light:#ececec;
  --white:#fff;
  --orange:#f08a1c;
}
*{margin:0;padding:0;box-sizing:border-box}
html,body{width:1200px;height:2556px;overflow:hidden}
body{font-family:"Open Sans",Arial,sans-serif;color:var(--ink);background:var(--white);position:relative}
.site-header{height:120px;display:flex;justify-content:space-between;align-items:center;padding:0 20px 0 22px}
.brand{font-family:"Oswald",Arial,sans-serif;font-weight:700;font-size:46px;letter-spacing:1px;color:var(--ink)}
.header-tools{display:flex;gap:46px;align-items:flex-start;margin-top:-14px}
.tool-label{font-family:"Oswald",Arial,sans-serif;font-size:15px;color:var(--red);font-weight:500;letter-spacing:.5px;margin-bottom:10px}
.social{display:flex;gap:14px}
.social span{width:18px;height:18px;background:#555;border-radius:3px;display:block}
.newsletter{display:flex}
.newsletter .field{width:170px;height:30px;border:1px solid #aaa;font-size:11px;color:#999;padding:7px 8px}
.newsletter .go{width:38px;height:30px;background:var(--dark);color:var(--orange);font-size:14px;text-align:center;line-height:30px}
.main-nav{height:28px;background:var(--nav);display:flex;gap:58px;padding-left:180px;align-items:center}
.main-nav a{font-family:"Oswald",Arial,sans-serif;color:var(--white);text-decoration:none;font-size:13px;letter-spacing:.6px}
.hero{position:relative;height:512px;background:linear-gradient(120deg,#6d6a66 0%,#9b9791 40%,#d9d6d2 70%,#8a8580 100%);color:var(--white);text-align:center}
.hero h1{font-family:"Oswald",Arial,sans-serif;font-size:58px;font-weight:700;letter-spacing:3px;padding-top:152px;text-shadow:0 2px 4px rgba(0,0,0,.45)}
.hero p{font-size:22px;font-weight:700;line-height:32px;width:920px;margin:8px auto 0;text-shadow:0 2px 4px rgba(0,0,0,.5)}
.hero .arrow{position:absolute;top:205px;width:40px;height:40px;border:2px solid var(--white);border-radius:50%}
.hero .arrow.left{left:74px}.hero .arrow.right{right:74px}
.hero .arrow svg{width:100%;height:100%}
.mission{height:415px;text-align:center;padding-top:56px}
.section-title{font-family:"Oswald",Arial,sans-serif;font-size:29px;font-weight:700;letter-spacing:.5px}
.rule{width:560px;height:2px;background:#333;margin:10px auto 22px}
.mission .body{font-size:14px;color:var(--grey);line-height:24px;width:1000px;margin:0 auto}
.mission .pitch{font-size:15px;color:var(--red);font-weight:700;line-height:26px;margin-top:22px}
.partners{display:flex;justify-content:center;gap:46px;align-items:center;margin-top:30px}
.partner{display:flex;align-items:center;gap:10px;font-family:"Oswald",Arial,sans-serif;font-weight:700;font-size:30px}
.partner.vmr{color:var(--red)}
.partner .mark{width:22px;height:22px;background:var(--red)}
.partner.steel{color:var(--ink);padding-left:46px;border-left:1px solid #bbb}
.partner.steel .mark{border-radius:50%;background:var(--ink);width:20px;height:20px}
.services{position:relative;height:690px;background:linear-gradient(180deg,#efefef,#e2e2e2)}
.services .section-title{text-align:center;padding-top:38px}
.services svg.hexes{position:absolute;left:0;top:0}
.photo-left{position:absolute;left:0;top:230px;width:290px;height:460px;background:linear-gradient(160deg,#dcc3a8,#3f7fb8 70%,#2d5c93)}
.photo-right{position:absolute;right:0;top:250px;width:270px;height:440px;background:linear-gradient(200deg,#c7a58c,#556070 60%,#2b2f36)}
.contact{height:640px;text-align:center;padding-top:38px}
.contact .owner{font-size:15px;font-weight:700;color:var(--red);margin-top:4px}
.contact .creds{font-size:15px;color:var(--grey);margin-top:14px}
.contact .creds span{margin:0 12px;color:#aaa}
.contact .cert{font-size:15px;color:var(--red);margin-top:14px}
.contact .line{font-size:15px;color:var(--grey);margin-top:14px;display:flex;justify-content:center;align-items:center;gap:8px}
.contact .line svg{width:14px;height:14px}
.map{position:absolute;left:60px;top:2140px;width:1080px;height:262px;background:linear-gradient(135deg,#ede8dd,#e4e0d6 50%,#d9e6d3)}
.site-footer{position:absolute;left:0;bottom:0;width:1200px;height:154px;background:var(--dark);text-align:center;padding-top:58px}
.site-footer nav{display:flex;justify-content:center;gap:30px}
.site-footer a{font-family:"Oswald",Arial,sans-serif;color:#ddd;font-size:12px;text-decoration:none;letter-spacing:.5px}
.site-footer p{color:#888;font-size:11px;margin-top:14px}
</style>
</head>
<body>
<header class="site-header">
  <div class="brand">KESTREL MOTION LLC</div>
  <div class="header-tools">
    <div>
      <div class="tool-label">CONNECT US</div>
      <div class="social"><span></span><span></span><span></span><span></span></div>
    </div>
    <div>
      <div class="tool-label">NEWSLETTER SIGN UP</div>
      <div class="newsletter"><div class="field">Enter Email Address</div><div class="go">&#10140;</div></div>
    </div>
  </div>
</header>
<nav class="main-nav">
  <a>HOME</a><a>SERVICES</a><a>PHYSICAL THERAPY</a><a>PERSONAL TRAINING</a><a>NUTRITION</a><a>CONTACT US</a>
</nav>
<section class="hero" role="img" aria-label="Athletes training with ropes and weights in a gym">
  <h1>KESTREL MOTION LLC</h1>
  <p>Kestrel Motion travels around the country and world treating athletes and people in the workforce that have Soft Tissue Injuries.</p>
  <div class="arrow left"><svg viewBox="0 0 40 40"><path d="M23 12l-8 8 8 8" fill="none" stroke="#fff" stroke-width="2.5"/></svg></div>
  <div class="arrow right"><svg viewBox="0 0 40 40"><path d="M17 12l8 8-8 8" fill="none" stroke="#fff" stroke-width="2.5"/></svg></div>
</section>
<section class="mission">
  <h2 class="section-title">KESTREL MOTION MISSION STATEMENT</h2>
  <div class="rule"></div>
  <p class="body">We are a company that specializes in Sports Therapy, Physical therapy, muscular rehab, nutrition plans, and personal training.<br>Kestrel Motion travels around the country and world treating athletes and people in the workforce that have Soft Tissue injuries.<br>We educate our patients on how to sustain a healthy lifestyle.</p>
  <p class="pitch">We build relationships with companies committed to the sustainable health of their employees and patrons.<br>We offer Corporate Health Solutions through VMR.</p>
  <div class="partners">
    <div class="partner vmr"><span class="mark"></span>VMR</div>
    <div class="partner steel"><span class="mark"></span>STEELRIDGE</div>
  </div>
</section>
<section class="services">
  <h2 class="section-title">OUR FEATURED SERVICES</h2>
  <div class="photo-left" role="img" aria-label="Therapist assisting an older man exercising on a blue ball"></div>
  <div class="photo-right" role="img" aria-label="Man and woman training with dumbbells"></div>
  <svg class="hexes" width="1200" height="690" viewBox="0 0 1200 690">
    <defs>
      <linearGradient id="gSports" x1="0" y1="0" x2="1" y2="1"><stop offset="0" stop-color="#e9c9b0"/><stop offset="1" stop-color="#8a8fa0"/></linearGradient>
      <linearGradient id="gPhys" x1="0" y1="0" x2="1" y2="1"><stop offset="0" stop-color="#d8b9a4"/><stop offset="1" stop-color="#b2463f"/></linearGradient>
      <linearGradient id="gNutri" x1="0" y1="0" x2="1" y2="1"><stop offset="0" stop-color="#e8d7a8"/><stop offset="1" stop-color="#7d8a3c"/></linearGradient>
      <linearGradient id="gRehab" x1="0" y1="0" x2="1" y2="1"><stop offset="0" stop-color="#c89a7c"/><stop offset="1" stop-color="#5a4638"/></linearGradient>
      <linearGradient id="gTrain" x1="0" y1="0" x2="1" y2="1"><stop offset="0" stop-color="#bfc3c8"/><stop offset="1" stop-color="#4b4f57"/></linearGradient>
    </defs>
    <g stroke="#fff" stroke-width="6" font-family="Oswald, Arial, sans-serif" font-weight="700" font-size="21" text-anchor="middle">
      <g role="img" aria-label="Sports therapy treatment on a client's leg">
        <polygon points="470,140 560,192 560,296 470,348 380,296 380,192" fill="url(#gSports)"/>
        <text x="470" y="252" fill="var(--orange)" stroke="none">SPORTS<tspan x="470" dy="24">THERAPY</tspan></text>
      </g>
      <g role="img" aria-label="Physical therapist stretching a client">
        <polygon points="730,140 820,192 820,296 730,348 640,296 640,192" fill="url(#gPhys)"/>
        <text x="730" y="252" fill="var(--orange)" stroke="none">PHYSICAL<tspan x="730" dy="24">THERAPY</tspan></text>
      </g>
      <g role="img" aria-label="Fresh healthy food for nutrition plans">
        <polygon points="600,252 690,304 690,408 600,460 510,408 510,304" fill="url(#gNutri)"/>
        <text x="600" y="362" fill="var(--orange)" stroke="none">NUTRITION<tspan x="600" dy="24">PLANS</tspan></text>
      </g>
      <g role="img" aria-label="Massage for muscular rehabilitation">
        <polygon points="470,364 560,416 560,520 470,572 380,520 380,416" fill="url(#gRehab)"/>
        <text x="470" y="476" fill="var(--orange)" stroke="none">MUSCULAR<tspan x="470" dy="24">REHAB</tspan></text>
      </g>
      <g role="img" aria-label="Personal trainer coaching a workout">
        <polygon points="730,364 820,416 820,520 730,572 640,520 640,416" fill="url(#gTrain)"/>
        <text x="730" y="476" fill="var(--orange)" stroke="none">PERSONAL<tspan x="730" dy="24">TRAINING</tspan></text>
      </g>
    </g>
  </svg>
</section>
<section class="contact">
  <h2 class="section-title">CONTACT US FOR PROGRAMS AND PRICING</h2>
  <div class="rule"></div>
  <p class="owner">MARCUS DELANE-OWNER/OPERATOR</p>
  <p class="creds">VMR Full Body Certified Practitioner<span>||</span>Fitness and Nutrition Consultant<span>||</span>Licensed Massage Therapist</p>
  <p class="cert">Certification # 50217</p>
  <p class="line"><svg viewBox="0 0 14 14"><path d="M7 1a4 4 0 0 0-4 4c0 3 4 8 4 8s4-5 4-8a4 4 0 0 0-4-4z" fill="var(--red)"/><circle cx="7" cy="5" r="1.5" fill="#fff"/></svg>2081 W. Carrow Ave Suite 412 Fairhaven, California 90210</p>
  <p class="line"><svg viewBox="0 0 14 14"><path d="M3 1l2 0 1 3-1.5 1a7 7 0 0 0 4.5 4.5l1-1.5 3 1v2a1 1 0 0 1-1 1A11 11 0 0 1 2 2a1 1 0 0 1 1-1z" fill="var(--red)"/></svg>(555) 014-2290</p>
</section>
<div class="map" role="img" aria-label="Street map showing the clinic location"></div>
<footer class="site-footer">
  <nav><a>HOME</a><a>SERVICES</a><a>PHYSICAL THERAPY</a><a>PERSONAL TRAINING</a><a>NUTRITION</a><a>CONTACT US</a></nav>
  <p>Copyright &copy; 2017, Kestrel Motion. All Rights Reserved</p>
</footer>
</body>
</html>
```